Web design

We need the design for the logo and website for a women fashion website. No coding required. The colors used should be neutral (maybe with a light touch of color), the style should be modern, slightly luxurious, not too crowded. The target market is young professionals who love trendy clothes.
Updates

Need extra days to review

Target Market(s)

Young professionals

Industry/Entity Type

Apparel

Number of Pages Required

5+ page

Font styles to use
Sans Serif
Other font styles liked:
• Montserrat, Engravers Gothic, Benton Sans, gotham-book

Colors

Designer to choose colors to be used in the design.

```html
<!DOCTYPE html>
<html lang="en">
<head>
<meta charset="utf-8">
<title>LUMA – Access your account</title>
<link href="https://fonts.googleapis.com/css2?family=Montserrat:wght@400;500;600;700&display=swap" rel="stylesheet">
<style>
:root{
  --ink:#1f1f24;
  --muted:#8f8f8f;
  --page:#f9f8f5;
  --footer:#f3f2f0;
  --white:#ffffff;
  --line:#e2e0dc;
  --sale:#e8412f;
  --green:#7cc68a;
  --badge:#e0a90d;
  --black:#000000;
}
*{margin:0;padding:0;box-sizing:border-box}
html,body{width:848px;height:1200px;overflow:hidden}
body{font-family:'Montserrat',sans-serif;color:var(--ink);background:var(--page);position:relative}
.t{position:absolute;transform:translateY(-50%);white-space:nowrap;line-height:1.2}
.r{right:71px}
.header{position:absolute;left:0;top:0;width:848px;height:53px;background:var(--white);border-bottom:1px solid var(--line)}
.nav{font-size:10px;font-weight:500}
.nav.sale{color:var(--sale)}
.brand{font-size:22px;font-weight:500;letter-spacing:1.5px}
.icon{position:absolute}
.main{position:absolute;left:0;top:53px;width:848px;height:901px;background:var(--page)}
.crumb{font-size:9px;font-weight:500;left:73px}
.side-title{font-size:9px;font-weight:500;left:116px}
.side-title.off{color:var(--muted)}
.side-desc{font-size:7.5px;left:116px;color:var(--ink)}
.side-desc.off{color:var(--muted)}
.h1{font-size:13.5px;font-weight:500;left:351px;letter-spacing:.2px}
.h2{font-size:10.5px;font-weight:500;left:351px}
.h2.bold{font-weight:600}
.body{font-size:8.5px;left:351px}
.body.big{font-size:10px}
.body.strong{font-weight:600}
.link{font-size:8.5px;text-decoration:underline;font-weight:500}
.dash{position:absolute;left:351px;width:426px;border-top:1px dashed var(--ink)}
.check{position:absolute;width:9px;height:9px;border:1px solid var(--ink)}
.field{position:absolute;top:848px;height:26px;border:1px solid #cfcdc9;background:var(--page);font-size:8px;padding-left:7px;line-height:24px}
.btn{position:absolute;left:676px;top:848px;width:101px;height:26px;background:var(--black);color:var(--white);font-size:7.5px;font-weight:700;text-align:center;line-height:26px;letter-spacing:.3px}
.footer{position:absolute;left:0;top:954px;width:848px;height:246px;background:var(--footer)}
.f-head{font-size:11.5px;font-weight:600;letter-spacing:.4px}
.f-link{font-size:10px}
.social{position:absolute;width:22px;height:22px;border:1px solid var(--ink);border-radius:50%}
.rule{position:absolute;left:74px;top:1144px;width:692px;border-top:1px solid #c9c7c3}
.copy{font-size:10px;left:0;width:848px;text-align:center}
</style>
</head>
<body>

<header class="header">
  <span class="t nav" style="left:71px;top:29px">Latest Arrivals</span>
  <span class="t nav" style="left:153px;top:29px">Clothes
    <svg width="7" height="5" viewBox="0 0 7 5"><path d="M1 1l2.5 2.5L6 1" fill="none" stroke="#1f1f24"/></svg></span>
  <span class="t nav" style="left:218px;top:29px">LUMA Club</span>
  <span class="t nav sale" style="left:291px;top:29px">On Sale</span>

  <span class="t brand" style="left:390px;top:29px">LUMA</span>

  <svg class="icon" style="left:650px;top:23px" width="12" height="12" viewBox="0 0 12 12"><circle cx="5" cy="5" r="4" fill="none" stroke="#1f1f24"/><path d="M8 8l3 3" stroke="#1f1f24"/></svg>
  <span class="t" style="left:681px;top:29px;font-size:8px;font-weight:500">ENG
    <svg width="6" height="4" viewBox="0 0 6 4"><path d="M1 1l2 2 2-2" fill="none" stroke="#1f1f24"/></svg></span>
  <svg class="icon" style="left:713px;top:21px" width="17" height="16" viewBox="0 0 17 16"><path d="M8.5 15S1 10 1 5a3.8 3.8 0 0 1 7.5-1A3.8 3.8 0 0 1 16 5c0 5-7.5 10-7.5 10z" fill="none" stroke="#1f1f24" stroke-width="1.1"/></svg>
  <svg class="icon" style="left:736px;top:20px" width="16" height="18" viewBox="0 0 16 18"><circle cx="8" cy="5" r="4" fill="none" stroke="#1f1f24"/><path d="M1 17c0-4 3-7 7-7s7 3 7 7" fill="none" stroke="#1f1f24"/></svg>
  <svg class="icon" style="left:759px;top:20px" width="20" height="18" viewBox="0 0 20 18"><path d="M2 6h11v11H2z" fill="none" stroke="#1f1f24"/><path d="M4.5 6V4a3 3 0 0 1 6 0v2" fill="none" stroke="#1f1f24"/><circle cx="14.5" cy="12.5" r="4" fill="#e0a90d"/><text x="14.5" y="14.6" font-size="5.5" text-anchor="middle" fill="#fff" font-family="Montserrat,sans-serif">0</text></svg>
</header>

<main class="main"></main>

<nav class="account-nav">
  <span class="t crumb" style="top:129px">My account / Access your account</span>

  <span style="position:absolute;left:71px;top:172px;width:14px;border-top:1px solid #1f1f24"></span>
  <svg class="icon" style="left:91px;top:163px" width="16" height="23" viewBox="0 0 16 23"><path d="M3 9V6a5 5 0 0 1 10 0v3" fill="none" stroke="#1f1f24"/><rect x="1" y="9" width="14" height="13" rx="1.5" fill="none" stroke="#1f1f24"/><circle cx="8" cy="14" r="2" fill="none" stroke="#1f1f24"/><path d="M8 16v3" stroke="#1f1f24"/></svg>
  <span class="t side-title" style="top:168px">ACCESS YOUR ACCOUNT</span>
  <span class="t side-desc" style="top:185px">From here you will be able to see and change the</span>
  <span class="t side-desc" style="top:196px">password or e-mail address with which you registered</span>

  <svg class="icon" style="left:86px;top:222px" width="26" height="13" viewBox="0 0 26 13"><path d="M1 6.5C5 1 21 1 25 6.5 21 12 5 12 1 6.5z" fill="none" stroke="#999"/><circle cx="13" cy="6.5" r="3" fill="none" stroke="#999"/></svg>
  <span class="t side-title off" style="top:227px">PERSONAL DATA</span>
  <span class="t side-desc off" style="top:243px">to facilitate the purchase process in the future and you</span>
  <span class="t side-desc off" style="top:254px">will be able to let us know if there are any changes in</span>
  <span class="t side-desc off" style="top:265px">your contact details.</span>

  <svg class="icon" style="left:89px;top:285px" width="20" height="24" viewBox="0 0 20 24"><rect x="2" y="1" width="16" height="22" rx="1" fill="none" stroke="#999"/><circle cx="10" cy="9" r="2.5" fill="none" stroke="#999"/><path d="M5.5 16c0-2.5 2-4 4.5-4s4.5 1.5 4.5 4z" fill="none" stroke="#999"/></svg>
  <span class="t side-title off" style="top:289px">ADDRESS</span>
  <span class="t side-desc off" style="top:305px">You can change the address or save it to make the</span>
  <span class="t side-desc off" style="top:315px">purchase process faster.</span>

  <svg class="icon" style="left:92px;top:337px" width="20" height="20" viewBox="0 0 20 20"><path d="M2 6l8-4 8 4v9l-8 4-8-4z M2 6l8 4 8-4 M10 10v9" fill="none" stroke="#999"/></svg>
  <span class="t side-title off" style="top:342px">ORDER HISTORY</span>
  <span class="t side-desc off" style="top:359px">Favorite stores</span>
</nav>

<section class="account-content">
  <span class="t h1" style="top:129px">ACCESS YOUR ACCOUNT</span>

  <span class="t h2" style="top:155px">PASSWORD</span>
  <span class="t link r" style="top:155px">Password change ✎</span>
  <span class="t body" style="top:168px;font-weight:700;letter-spacing:.5px">***************</span>
  <span class="t body" style="top:186px">If you want to change your password, click on "Change password" and enter the required information.</span>
  <span class="dash" style="top:208px"></span>

  <span class="t h2" style="top:236px">YOUR EMAIL ADDRESS</span>
  <span class="t link r" style="top:236px">CHANGE EMAIL ✎</span>
  <span class="t body big" style="top:252px">info@username.com</span>
  <span class="t h2 bold" style="top:277px">Newsletter</span>
  <span class="t body" style="top:296px">Sign up for the Newsletter and you will receive the latest news, information about promotions and</span>
  <span class="t body" style="top:312px">discounts on vestra.com</span>
  <span class="t body" style="top:332px">I have read the Privacy Policy and would like to receive personalized business news and communications</span>
  <span class="t body" style="top:347px">from VESTRA by email and other means.</span>

  <svg class="icon" style="left:352px;top:368px" width="10" height="10" viewBox="0 0 10 10"><rect x=".5" y=".5" width="9" height="9" fill="none" stroke="#1f1f24"/><path d="M2.5 5l2 2 3-4" fill="none" stroke="#1f1f24"/></svg>
  <span class="t h2" style="left:366px;top:373px;font-size:9.5px">ACTIVATE</span>
  <span class="check" style="left:424px;top:368px"></span>
  <span class="t h2" style="left:438px;top:373px;font-size:9.5px">INACTIVATE</span>
  <span style="position:absolute;left:351px;top:382px;width:68px;border-top:1px solid var(--green)"></span>
  <span class="dash" style="top:408px"></span>

  <span class="t h1" style="top:440px">PERSONAL DATA</span>
  <span class="t body" style="top:464px">At LUMA we take your privacy seriously and are committed to protecting your personal information.</span>
  <span class="t body" style="top:477px">The <u>Privacy Policy</u> learn more about how we protect and use your data.</span>
  <span class="t body strong" style="top:502px">You will be able to access and modify personal data (name, billing address, phone ...)</span>
  <span class="t h2" style="top:530px">BILLING DATA</span>
  <span class="t link r" style="top:530px">Password change ✎</span>
  <span class="t h2 bold" style="top:553px">Titanium</span>
  <span class="t body big" style="top:568px">info@username.com</span>
  <span class="t body big" style="top:590px">Romania</span>
  <span class="t body big" style="top:604px">Mobile phone: +40</span>
  <span class="dash" style="top:634px"></span>

  <span class="t h1" style="top:664px">MY ADDRESSES</span>
  <span class="t body" style="top:686px">ADD A NEW ADDRESS</span>
  <span class="dash" style="top:718px"></span>

  <span class="t h1" style="top:749px">ORDER HISTORY</span>
  <span class="t body" style="top:771px">Here you will be able to save the addresses of your favorite vestra stores which will facilitate the</span>
  <span class="t body" style="top:784px">online shopping process</span>
  <span class="dash" style="top:809px"></span>

  <span class="t h2 bold" style="top:831px">Order Details</span>
  <span class="field" style="left:350px;width:101px">order number</span>
  <span class="field" style="left:458px;width:102px">date</span>
  <span class="field" style="left:567px;width:102px">status</span>
  <span class="btn">DOWNLOAD INVOICE</span>
</section>

<footer class="footer"></footer>
<div class="footer-content">
  <span class="t brand" style="left:67px;top:1031px;font-size:34px;letter-spacing:2px">LUMA</span>

  <span class="t f-head" style="left:311px;top:1015px">HELP</span>
  <span class="t f-link" style="left:310px;top:1042px">Terms &amp; Conditions</span>
  <span class="t f-link" style="left:310px;top:1061px">Privacy Policy</span>
  <span class="t f-link" style="left:310px;top:1080px">Returns/exchanges</span>
  <span class="t f-link" style="left:310px;top:1099px">Delivery Information</span>
  <span class="t f-link" style="left:310px;top:1118px">FAQ</span>

  <span class="t f-head" style="left:517px;top:1015px">SHOP</span>
  <span class="t f-link" style="left:516px;top:1042px">Tops</span>
  <span class="t f-link" style="left:516px;top:1061px">Bootoms</span>
  <span class="t f-link" style="left:516px;top:1080px">Intimates</span>
  <span class="t f-link" style="left:516px;top:1099px">Dresses</span>
  <span class="t f-link" style="left:516px;top:1118px">Swim</span>

  <span class="t f-head" style="left:676px;top:1015px">CONTACT US</span>
  <svg class="icon" style="left:677px;top:1029px" width="11" height="8" viewBox="0 0 11 8"><rect width="11" height="8" fill="#1f1f24"/><path d="M0 0l5.5 4.5L11 0" fill="none" stroke="#f3f2f0"/></svg>
  <span class="t f-link" style="left:692px;top:1033px">info@luma.com</span>
  <span class="t f-head" style="left:676px;top:1063px">FOLLOW US</span>
  <span class="social" style="left:673px;top:1079px"></span>
  <span class="social" style="left:699px;top:1079px"></span>
  <span class="social" style="left:725px;top:1079px"></span>
  <span class="social" style="left:751px;top:1079px"></span>

  <span class="rule"></span>
  <span class="t copy" style="top:1166px">Terms &amp; Conditions, Privacy Policy and @2021 followed by luma.</span>
</div>

</body>
</html>
```